****Business Card Design for Quarrystone Development. Design based around attached logo/company name

I’m looking for business card design for my company Quarrystone Development Group,LLC. Design should be professional, sharp and minimal. Outside of the attached logos, greyscale colors for remainder of cards. My thoughts are two-sided card with attached logo on one side and my info on the other but open to one-sided as well with right design.
Target Market(s)
Real estate professionals including banks, private investors, property owners, developers, commercial tenants like Brewlantern, Grovika or Tanquist’s.
Industry/Entity Type
Commercial real estate development and investments.
Contact Information for Business Card
Name, title, email, phone #’s, web address and physical address
Font styles to use
Other font styles liked:
- Helvetica, Garamond, etc
Colors
Designer to choose only greyscale colors for use in the design.
Requirements
Must have
- Attached logo first or second options.
Nice to have
- Two sided card with logo on one side. Attached Logo/company name can be laid out any way that flows as long as it’s legible.name
Should not have
- No loud colors. ***Please do not include logo, I have removed the company design with a logo image.

```html
<!DOCTYPE html>
<html lang="en">
<head>
<meta charset="utf-8">
<title>Quarrystone Development – Business Card</title>
<link href="https://fonts.googleapis.com/css2?family=Libre+Baskerville:wght@700&family=Arimo:wght@400&display=swap" rel="stylesheet">
<style>
  :root {
    --page-bg: #e3e3e3;
    --card-bg: #5b6474;
    --ink-light: #eef0f3;
    --rule: #8a92a0;
  }
  html, body {
    margin: 0;
    width: 1200px;
    height: 1059px;
    overflow: hidden;
    background: var(--page-bg);
  }
  .card {
    position: absolute;
    left: 222px;
    top: 310px;
    width: 756px;
    height: 430px;
    border-radius: 24px;
    background: var(--card-bg);
    color: var(--ink-light);
  }
  .brand {
    position: absolute;
    left: 62px;
    top: 186px;
    width: 292px;
    text-align: center;
    font-family: Arimo, Helvetica, Arial, sans-serif;
    font-weight: 400;
    color: var(--ink-light);
  }
  .brand-name {
    display: block;
    font-size: 34px;
    line-height: 38px;
    letter-spacing: 1px;
  }
  .brand-sub {
    display: block;
    margin-top: 4px;
    font-size: 13px;
    line-height: 16px;
    letter-spacing: 2px;
  }
  .divider {
    position: absolute;
    left: 378px;
    top: 121px;
    width: 1px;
    height: 189px;
    background: var(--rule);
  }
  .contact {
    position: absolute;
    left: 411px;
    top: 116px;
    font-family: Arimo, Helvetica, Arial, sans-serif;
    font-size: 17px;
    line-height: 21px;
  }
  .person-name {
    margin: 0;
    font-family: "Libre Baskerville", Georgia, serif;
    font-weight: 700;
    font-size: 20px;
    line-height: 22px;
    letter-spacing: 0.3px;
  }
  .person-title { margin: 0 0 18px; }
  .address { margin: 0 0 21px; font-style: normal; }
  .channels { list-style: none; margin: 0; padding: 0; }
  .channels li {
    display: flex;
    align-items: center;
    height: 26px;
  }
  .channels svg {
    width: 14px;
    height: 14px;
    margin-right: 7px;
    fill: var(--ink-light);
  }
</style>
</head>
<body>
  <section class="card">
    <div class="brand">
      <span class="brand-name">QUARRYSTONE</span>
      <span class="brand-sub">DEVELOPMENT GROUP, LLC</span>
    </div>
    <div class="divider"></div>
    <div class="contact">
      <p class="person-name">DANIEL OSTROW</p>
      <p class="person-title">Founder/CEO</p>
      <address class="address">2216 Harlow Ridge Road<br>Westbrook AB 5520</address>
      <ul class="channels">
        <li>
          <svg viewBox="0 0 16 16" aria-hidden="true"><path d="M3.5 1.5l2.4 2.9-1.4 1.6c.9 1.9 2.3 3.3 4.2 4.2l1.6-1.4 2.9 2.4-1.3 2.3C7 13.3 2.7 9 2.2 3z"/></svg>
          (555)-310-2846
        </li>
        <li>
          <svg viewBox="0 0 16 16" aria-hidden="true"><path d="M1 3h14v1.6L8 9 1 4.6z M1 6.4l7 4.4 7-4.4V13H1z"/></svg>
          info@quarrystonedevelopment.com
        </li>
        <li>
          <svg viewBox="0 0 16 16" aria-hidden="true"><path d="M8 1a7 7 0 1 0 0 14A7 7 0 0 0 8 1zm0 1.5c.9 0 1.9 1.6 2.2 4.5H5.8C6.1 4.1 7.1 2.5 8 2.5zM2.6 8.5h1.9c.1 1.7.5 3.2 1.1 4.2a5.5 5.5 0 0 1-3-4.2zm0-1.5a5.5 5.5 0 0 1 3-4.2C5 3.8 4.6 5.3 4.5 7zm5.4 6.5c-.9 0-1.9-1.6-2.2-5h4.4c-.3 3.4-1.3 5-2.2 5zm2.4-.8c.6-1 1-2.5 1.1-4.2h1.9a5.5 5.5 0 0 1-3 4.2zM11.5 7c-.1-1.7-.5-3.2-1.1-4.2a5.5 5.5 0 0 1 3 4.2z"/></svg>
          www.quarrystonedevelopment.com
        </li>
      </ul>
    </div>
  </section>
</body>
</html>
```